RESIDENTIAL CONSTRUCTION

We are a company that specializes in building custom residential homes, the design should also emphasize that quality and service is our priority.

Industry/Entity Type

Construction Company

Contact Information for Business Card

Contact Person: Marcus Lindqvist
Company Address: 273 West Alder Ave San Jose , Ca 95380
Phone Number : 408-731-2946
Email Address: Stoneridgehomes517@mailvista.net

Font styles to use
Sans Serif

Colors
ec1f27

Requirements
Must have
• CSLB # 7362015
Nice to have
• needs to have same color as logo i uploaded, we will be printing these on a clear plastic card.

```html
<!DOCTYPE html>
<html lang="en">
<head>
<meta charset="utf-8">
<title>Stoneridge Homes – Business Card</title>
<link rel="stylesheet" href="https://fonts.googleapis.com/css2?family=Roboto:wght@400;500&family=Roboto+Condensed:wght@700&display=swap">
<style>
  :root {
    --brand-red: #c51d2e;
    --brand-red-light: #d5495a;
    --card-white: #ffffff;
    --text-grey: #5a5a5a;
    --backdrop: #e9e7e3;
  }
  * { margin: 0; padding: 0; box-sizing: border-box; }
  html, body {
    width: 1200px;
    height: 950px;
    overflow: hidden;
    background: var(--backdrop);
  }
  .canvas {
    position: relative;
    width: 1200px;
    height: 950px;
  }
  .business-card {
    position: absolute;
    left: 75px;
    top: 175px;
    width: 1050px;
    height: 600px;
    background: var(--card-white);
    box-shadow: 0 6px 24px rgba(0,0,0,0.12);
    overflow: hidden;
  }
  .brand-mark {
    position: absolute;
    left: 0;
    right: 0;
    top: 175px;
    display: flex;
    justify-content: center;
    align-items: center;
    gap: 16px;
  }
  .brand-square {
    width: 34px;
    height: 34px;
    background: var(--brand-red);
  }
  .brand-name {
    font-family: "Roboto Condensed", "Arial Narrow", sans-serif;
    font-weight: 700;
    font-size: 58px;
    letter-spacing: 1px;
    text-transform: uppercase;
    color: var(--brand-red);
    line-height: 1;
  }
  .name-band {
    position: absolute;
    left: 0;
    right: 0;
    top: 330px;
    height: 78px;
    background: linear-gradient(90deg, var(--brand-red-light) 0%, var(--brand-red) 45%, var(--brand-red) 100%);
    display: flex;
    align-items: center;
    padding-left: 400px;
  }
  .contact-name {
    font-family: "Roboto Condensed", "Arial Narrow", sans-serif;
    font-weight: 700;
    font-size: 38px;
    letter-spacing: 0.5px;
    text-transform: uppercase;
    color: var(--card-white);
  }
  .contact-list {
    position: absolute;
    left: 70px;
    top: 450px;
    list-style: none;
    font-family: "Roboto", Arial, sans-serif;
    font-size: 23px;
    color: var(--text-grey);
  }
  .contact-list li {
    display: flex;
    align-items: center;
    gap: 14px;
    height: 34px;
  }
  .contact-icon {
    width: 20px;
    height: 20px;
    flex: none;
  }
  .company-details {
    position: absolute;
    right: 60px;
    top: 445px;
    text-align: right;
    font-family: "Roboto", Arial, sans-serif;
    font-size: 24px;
    line-height: 36px;
    color: var(--text-grey);
  }
  .license-number { margin-top: 18px; }
</style>
</head>
<body>
<main class="canvas">
  <article class="business-card">
    <div class="brand-mark">
      <span class="brand-square"></span>
      <span class="brand-name">Stoneridge Homes</span>
    </div>

    <div class="name-band">
      <h1 class="contact-name">Marcus Lindqvist</h1>
    </div>

    <ul class="contact-list">
      <li>
        <svg class="contact-icon" viewBox="0 0 20 20" aria-hidden="true">
          <path d="M5 2l3 4-2 2c1 2.5 3.5 5 6 6l2-2 4 3-2 3C9 18 2 11 2 4z" fill="var(--brand-red)"/>
        </svg>
        <span>408-731-2946</span>
      </li>
      <li>
        <svg class="contact-icon" viewBox="0 0 20 20" aria-hidden="true">
          <rect x="1" y="4" width="18" height="12" fill="var(--brand-red)"/>
          <path d="M1 4l9 7 9-7" fill="none" stroke="#fff" stroke-width="1.6"/>
        </svg>
        <span>Stoneridgehomes517@mailvista.net</span>
      </li>
      <li>
        <svg class="contact-icon" viewBox="0 0 20 20" aria-hidden="true">
          <circle cx="10" cy="10" r="9" fill="var(--brand-red)"/>
          <path d="M1 10h18M10 1c-4 4-4 14 0 18M10 1c4 4 4 14 0 18" fill="none" stroke="#fff" stroke-width="1.2"/>
        </svg>
        <span>www.stoneridgehomes.net</span>
      </li>
    </ul>

    <address class="company-details">
      <div>273 West Alder Ave San Jose</div>
      <div>Ca 95380</div>
      <div class="license-number">CSLB # 7362015</div>
    </address>
  </article>
</main>
</body>
</html>
```